Brevlon Website Design - Wordpress

Need a website WordPress design for our existing website that we just stood up. The logo is already in place and name. Brevlon.example We are a company which makes connections with our clients through educating them and providing networking events. We would like for the website to show a VIP/special feel to it.

Target Market(s)

Business executives and employees. Age group 26-65 in the following sectors:
- Technology
- Human Resources
- Finance
- Sales

Industry/Entity Type

Technical Service

Number of Pages Required

4 page

Font styles to use
Sans Serif

Requirements
Must have
• Must be something for Wordpress
Nice to have
• Would like this to be professional but look cutting edge and VIP.

```html
<!DOCTYPE html>
<html lang="en">
<head>
<meta charset="utf-8">
<title>Brevlon — Expand Your Business</title>
<link href="https://fonts.googleapis.com/css2?family=Open+Sans:wght@400;600;700;800&family=Raleway:wght@400;500;600;700&family=Montserrat:wght@500;600;700&display=swap" rel="stylesheet">
<style>
:root{
  --navy:#0b4474;
  --blue:#0f5f8c;
  --sky:#0a95de;
  --red:#c9252c;
  --purple:#7a3a8c;
  --gold:#e0a91c;
  --green:#3b9a3f;
  --ink:#1d1d1f;
  --text:#555a60;
  --muted:#8a8f94;
  --panel:#efefef;
  --card:#f4f4f4;
  --white:#ffffff;
  --dark:#1f2124;
}
*{box-sizing:border-box;margin:0;padding:0}
html,body{width:1200px;height:3727px;overflow:hidden}
body{position:relative;background:var(--white);font-family:"Open Sans",Arial,sans-serif;color:var(--text)}

/* header */
.site-header{position:absolute;left:0;top:0;width:1200px;height:72px;background:var(--white);z-index:3}
.brand{position:absolute;left:174px;top:18px;display:flex;align-items:center;gap:10px}
.brand-mark{width:30px;height:30px;background:var(--navy)}
.brand-name{font-family:"Montserrat",sans-serif;font-weight:600;font-size:26px;letter-spacing:3px;color:var(--navy)}
.main-nav{position:absolute;left:640px;top:27px;display:flex;gap:44px;font-size:15px;color:var(--ink)}

/* hero */
.hero-shape{position:absolute;left:0;top:72px;z-index:1}
.hero-art{position:absolute;left:560px;top:140px;width:610px;height:540px;border-radius:24px;
  background:linear-gradient(160deg,rgba(255,255,255,.45),rgba(200,225,245,.75) 55%,rgba(255,255,255,.9));z-index:2}
.hero-copy{position:absolute;left:164px;top:205px;width:560px;color:var(--white);z-index:2}
.hero-title{font-weight:800;font-size:50px;line-height:64px;letter-spacing:1px;white-space:nowrap}
.hero-text{margin-top:26px;width:370px;font-size:18px;line-height:27px}
.btn{display:inline-block;color:var(--white);font-family:"Montserrat",sans-serif;font-weight:600;text-align:center;border-radius:3px}
.btn-join{position:absolute;left:161px;top:480px;width:150px;height:44px;line-height:44px;background:var(--red);font-size:16px;z-index:2}
.tech-bar{position:absolute;left:161px;top:703px;width:877px;height:72px;border-radius:10px;background:var(--gold);
  box-shadow:0 6px 14px rgba(0,0,0,.25);z-index:2;display:flex;align-items:center;color:var(--white)}
.tech-bar .lead{margin-left:22px;font-family:"Raleway",sans-serif;font-weight:500;font-size:32px}
.tech-bar .call{margin-left:auto;font-size:17px;margin-right:14px}
.tech-bar .icon{width:40px;height:40px;border:2px solid var(--white);border-radius:50%;display:flex;align-items:center;justify-content:center;margin-right:10px}
.tech-bar .num{font-weight:600;font-size:26px;margin-right:30px}

/* section headings */
.sec-head{position:absolute;display:flex;align-items:center;gap:14px;font-family:"Raleway",sans-serif;font-size:44px;font-weight:500;color:var(--ink)}
.sec-head .sq{width:40px;height:40px;background:var(--ink)}
.sec-head .accent{color:var(--red);margin-left:-4px}
.center{left:0;width:1200px;justify-content:center}
.intro{position:absolute;left:0;width:1200px;text-align:center;font-size:13px;line-height:21px;color:var(--text)}

/* about */
.values-diagram{position:absolute;left:170px;top:900px}
.value-label{position:absolute;font-size:17px;line-height:22px;color:var(--ink);transform:translateX(-50%);white-space:nowrap}
.about-copy{position:absolute;left:611px;top:1040px;width:480px;font-size:12.5px;line-height:19px}
.about-copy p{margin-bottom:17px}
.btn-unique{position:absolute;left:611px;top:1287px;width:134px;height:45px;line-height:45px;background:var(--blue);font-size:14px}

/* expands */
.expands{position:absolute;left:0;top:1428px;width:1200px;height:597px;background:var(--panel)}
.tagline{position:absolute;left:0;width:1200px;text-align:center;font-family:"Montserrat",sans-serif;font-weight:600;font-size:13px;color:var(--blue)}
.expand-item{position:absolute;width:200px;text-align:center}
.expand-icon{width:80px;height:80px;margin:0 auto;border-radius:50%;border:5px solid #dcdcdc;display:flex;align-items:center;justify-content:center}
.expand-icon span{width:58px;height:58px;border-radius:50%;display:flex;align-items:center;justify-content:center}
.expand-item h3{margin-top:12px;font-family:"Montserrat",sans-serif;font-weight:700;font-size:16px;color:var(--ink)}
.expand-item p{margin-top:8px;font-size:11.5px;line-height:18px}
.btn-value{position:absolute;left:532px;top:1918px;width:134px;height:45px;line-height:45px;background:var(--green);font-size:14px}

/* events */
.event-card{position:absolute;top:2256px;width:278px;height:440px;background:var(--card)}
.event-photo{height:191px}
.event-body{padding:14px 12px}
.event-title{font-size:14px;line-height:22px;font-weight:400;color:var(--ink);height:46px}
.event-date{margin-top:8px;font-family:"Montserrat",sans-serif;font-weight:700;font-size:10.5px;color:var(--blue)}
.event-text{margin-top:8px;font-size:11px;line-height:17px}
.event-group{margin-top:6px;font-size:11px;font-weight:600;color:var(--ink)}
.event-foot{position:absolute;left:12px;right:12px;bottom:22px;display:flex;align-items:center;font-size:12px;color:var(--ink)}
.event-foot svg{margin-right:8px}
.btn-more{margin-left:auto;width:96px;height:30px;line-height:30px;background:var(--gold);font-size:10.5px}

/* strategy */
.strategy-box{position:absolute;top:2925px;width:204px;height:164px;color:var(--white);padding:14px 12px}
.strategy-box h4{display:flex;align-items:center;gap:8px;font-family:"Montserrat",sans-serif;font-weight:600;font-size:14px}
.strategy-box h4 span{width:30px;height:30px;border:2px solid var(--white);border-radius:50%;flex:none}
.strategy-box p{margin-top:10px;font-size:10.5px;line-height:16px}

/* footer */
.site-footer{position:absolute;left:0;top:3185px;width:1200px;height:542px;
  background:linear-gradient(180deg,#2a2c2f,#1b1c1e 60%,#141516)}
.footer-head{color:var(--white)}
.field{position:absolute;height:37px;background:var(--white);border-radius:2px;font-size:11px;color:#666;padding:11px 10px;display:flex;justify-content:space-between}
.field i{width:14px;height:14px;border:1.5px solid #999;border-radius:2px;display:block}
.btn-submit{position:absolute;left:161px;top:3568px;width:98px;height:35px;line-height:35px;background:var(--red);font-size:14px}
.social{position:absolute;top:3392px;left:713px;display:flex;gap:14px}
.social span{width:40px;height:40px;border-radius:50%;background:#4a4c50}
.social span:first-child{background:var(--green)}
.footer-nav{position:absolute;left:655px;top:3462px;display:flex;gap:12px;font-size:14px;color:var(--white)}
.footer-contact{position:absolute;top:3516px;display:flex;align-items:center;gap:10px;font-size:13px;color:var(--white)}
.footer-contact b{width:26px;height:26px;border:1.5px solid var(--white);border-radius:50%;display:flex;align-items:center;justify-content:center}
.footer-rule{position:absolute;left:161px;top:3665px;width:878px;height:1px;background:rgba(255,255,255,.2)}
.copyright{position:absolute;left:0;top:3688px;width:1200px;text-align:center;font-size:11px;color:#cfcfcf}
.copyright em{font-style:normal;color:var(--gold)}
</style>
</head>
<body>

<header class="site-header">
  <div class="brand"><span class="brand-mark"></span><span class="brand-name">BREVLON</span></div>
  <nav class="main-nav"><span>Events</span><span>Expand</span><span>X</span><span>About</span><span>Connect</span></nav>
</header>

<svg class="hero-shape" width="1200" height="760" viewBox="0 0 1200 760">
  <defs>
    <linearGradient id="heroGrad" x1="0" y1="0" x2="1" y2="0.2">
      <stop offset="0" stop-color="#0b3f6c"/>
      <stop offset="0.55" stop-color="#0a6fb6"/>
      <stop offset="1" stop-color="#0aa0e8"/>
    </linearGradient>
  </defs>
  <path d="M0 0H1200V520C1040 560 900 520 760 600C640 670 520 560 380 640C280 700 160 760 0 740Z" fill="url(#heroGrad)"/>
</svg>
<div class="hero-art" role="img" aria-label="Isometric illustration of rising white bar columns, a browser window and a checklist on a clipboard"></div>

<div class="hero-copy">
  <h1 class="hero-title">EXPAND YOUR<br>BUSINESS</h1>
  <p class="hero-text">BREVLON provides impactful connection opportunities to help educate, equip and expand you and your business</p>
</div>
<a class="btn btn-join">JOIN NOW</a>

<div class="tech-bar">
  <span class="lead">Need Technical Services??</span>
  <span class="call">Call us now</span>
  <span class="icon"><svg width="20" height="20" viewBox="0 0 24 24"><path d="M6.6 10.8a15 15 0 006.6 6.6l2.2-2.2a1 1 0 011-.25 11.4 11.4 0 003.6.57 1 1 0 011 1V20a1 1 0 01-1 1A17 17 0 013 4a1 1 0 011-1h3.5a1 1 0 011 1c0 1.25.2 2.45.57 3.6a1 1 0 01-.25 1z" fill="#fff"/></svg></span>
  <span class="num">+1-555-010-7890</span>
</div>

<!-- about -->
<svg class="values-diagram" width="420" height="440" viewBox="0 0 420 440">
  <circle cx="205" cy="241" r="150" fill="none" stroke="#555" stroke-width="1.5" stroke-dasharray="6 6"/>
  <circle cx="205" cy="241" r="106" fill="none" stroke="#555" stroke-width="1.5" stroke-dasharray="6 6"/>
  <circle cx="205" cy="241" r="56" fill="#fff" stroke="#ddd" stroke-width="4"/>
  <g fill="#fff" stroke="#e2e2e2" stroke-width="5">
    <circle cx="205" cy="101" r="43"/><circle cx="65" cy="241" r="43"/>
    <circle cx="345" cy="241" r="43"/><circle cx="205" cy="381" r="43"/>
  </g>
  <circle cx="205" cy="101" r="16" fill="#c9252c"/>
  <circle cx="65" cy="241" r="16" fill="#0f5f8c"/>
  <circle cx="345" cy="241" r="16" fill="#e0a91c"/>
  <circle cx="205" cy="381" r="16" fill="#7a3a8c"/>
</svg>
<span class="value-label" style="left:375px;top:920px">Virtue</span>
<span class="value-label" style="left:220px;top:1198px">Ownership</span>
<span class="value-label" style="left:530px;top:1198px">Appreciation</span>
<span class="value-label" style="left:375px;top:1346px">Respect</span>

<h2 class="sec-head" style="left:611px;top:950px"><span class="sq"></span>About <span class="accent">Brevlon</span></h2>
<div class="about-copy">
  <p>Our team is an unusual mix. We're globally experienced, technically capable, community focused and highly fruitful. The four core values above inform everything we do.</p>
  <p>Our special sauce is knowing how to fuse structure and productivity with relationship and creativity. Our special sauce is knowing how to fuse structure and productivity with relationship and creativity.</p>
  <p>Our special sauce is knowing how to fuse structure and productivity with relationship and creativity.</p>
</div>
<a class="btn btn-unique">X • UNIQUE</a>

<!-- expands -->
<section class="expands"></section>
<h2 class="sec-head center" style="top:1505px"><span class="sq"></span>Our <span class="accent">Expands</span></h2>
<p class="tagline" style="top:1581px">It's about our unique X Strategy</p>
<p class="intro" style="top:1606px">BREVLON provides impactful connection opportunities to help educate, equip and<br>expand you and your business</p>

<div class="expand-item" style="left:161px;top:1687px">
  <div class="expand-icon"><span style="background:var(--blue)"><svg width="28" height="22" viewBox="0 0 28 22"><rect x="2" y="2" width="24" height="15" fill="none" stroke="#fff" stroke-width="2"/><path d="M9 21h10" stroke="#fff" stroke-width="2"/></svg></span></div>
  <h3>Educate</h3>
  <p>At BREVLON, we provide effective training and learning as the foundation for building a healthy, successful company.</p>
</div>
<div class="expand-item" style="left:385px;top:1687px">
  <div class="expand-icon"><span style="background:var(--red)"><svg width="26" height="26" viewBox="0 0 26 26"><circle cx="13" cy="13" r="9" fill="none" stroke="#fff" stroke-width="2"/><circle cx="13" cy="13" r="3" fill="#fff"/></svg></span></div>
  <h3>Equip</h3>
  <p>Through our connected ecosystem of companies, we'll help find the right partners for equipping you to move forward.</p>
</div>
<div class="expand-item" style="left:611px;top:1687px">
  <div class="expand-icon"><span style="background:var(--gold)"><svg width="28" height="26" viewBox="0 0 28 26"><circle cx="14" cy="5" r="3.5" fill="#fff"/><circle cx="5" cy="20" r="3.5" fill="#fff"/><circle cx="23" cy="20" r="3.5" fill="#fff"/><path d="M14 9L6 17M14 9l8 8M8 20h12" stroke="#fff" stroke-width="1.8"/></svg></span></div>
  <h3>Exchange</h3>
  <p>We connect you with others who have successfully implemented our X Strategy to facilitate growth in their business.</p>
</div>
<div class="expand-item" style="left:837px;top:1687px">
  <div class="expand-icon"><span style="background:var(--purple)"><svg width="26" height="26" viewBox="0 0 26 26"><rect x="3" y="3" width="20" height="20" fill="none" stroke="#fff" stroke-width="2"/><path d="M8 18L18 8M12 8h6v6" stroke="#fff" stroke-width="2" fill="none"/></svg></span></div>
  <h3>Expand</h3>
  <p>Our goal is to help you and your business increase productivity and scale through effective strategy and healthy culture.</p>
</div>
<a class="btn btn-value">X • VALUE</a>

<!-- events -->
<h2 class="sec-head center" style="top:2095px"><span class="sq"></span>Our <span class="accent">Events</span></h2>
<p class="intro" style="top:2172px">BREVLON grows you and your company through relevant education and networking<br>events. We help you make the connections you need to expand.</p>

<article class="event-card" style="left:161px">
  <div class="event-photo" role="img" aria-label="Close-up photo of brass clockwork gears" style="background:linear-gradient(135deg,#6b5a3a,#c9a45a 45%,#3d3a36)"></div>
  <div class="event-body">
    <h3 class="event-title">Online Workshop - Dimension reduction: From modeling to…</h3>
    <p class="event-date">MON, FEB 3, 12:30 PM</p>
    <p class="event-text">Join your technology peers for BREVLON's Battle Scars and Battle Plans dinner discussing Disaster Recovery, Backup, and Cloud.</p>
    <p class="event-group">Metro AI Tech Talk Group</p>
  </div>
  <div class="event-foot"><svg width="14" height="18" viewBox="0 0 14 18"><path d="M7 1a6 6 0 016 6c0 4.5-6 10-6 10S1 11.5 1 7a6 6 0 016-6z" fill="none" stroke="#c9252c" stroke-width="1.6"/><circle cx="7" cy="7" r="2" fill="#c9252c"/></svg>Location</div>
</article>
<article class="event-card" style="left:462px">
  <div class="event-photo" role="img" aria-label="Photo of a hand touching a glowing blue digital interface" style="background:linear-gradient(135deg,#061c3a,#0d5a9c 50%,#0a2a52)"></div>
  <div class="event-body">
    <h3 class="event-title">Decentralized App Development Workshop</h3>
    <p class="event-date">MON, MAR 2, 12:30 PM</p>
    <p class="event-text">Join your technology peers for BREVLON's Battle Scars and Battle Plans dinner discussing Disaster Recovery, Backup, and Cloud.</p>
    <p class="event-group">Metro Ledger Protocol Developers</p>
  </div>
  <div class="event-foot"><svg width="14" height="18" viewBox="0 0 14 18"><path d="M7 1a6 6 0 016 6c0 4.5-6 10-6 10S1 11.5 1 7a6 6 0 016-6z" fill="none" stroke="#c9252c" stroke-width="1.6"/><circle cx="7" cy="7" r="2" fill="#c9252c"/></svg>Location<a class="btn btn-more">READ MORE</a></div>
</article>
<article class="event-card" style="left:763px">
  <div class="event-photo" role="img" aria-label="Photo of a large parliamentary assembly hall with curved rows of seats" style="background:linear-gradient(180deg,#4a3328,#8c5a3c 50%,#5a2e24)"></div>
  <div class="event-body">
    <h3 class="event-title">Why Female Led Ventures Will Never Break Into the Vc Deal.</h3>
    <p class="event-date">MON, MAR 3, 12:30 PM</p>
    <p class="event-text">Join your technology peers for BREVLON's Battle Scars and Battle Plans dinner discussing Disaster Recovery, Backup, and Cloud.</p>
    <p class="event-group">Women in Ledger Tech - Nordics</p>
  </div>
  <div class="event-foot"><svg width="14" height="18" viewBox="0 0 14 18"><path d="M7 1a6 6 0 016 6c0 4.5-6 10-6 10S1 11.5 1 7a6 6 0 016-6z" fill="none" stroke="#c9252c" stroke-width="1.6"/><circle cx="7" cy="7" r="2" fill="#c9252c"/></svg>Location<a class="btn btn-more">READ MORE</a></div>
</article>

<!-- strategy -->
<h2 class="sec-head center" style="top:2776px"><span class="sq"></span>Our <span class="accent">X Strategy</span></h2>
<p class="intro" style="top:2852px">We use a green diamond in our logo to represent your company's culture. Green<br>speaks of health. And growth. And life.</p>

<div class="strategy-box" style="left:161px;background:var(--blue)"><h4><span></span>Mind Thought</h4><p>What we believe shapes how we behave. And our behavior shapes who we become. Because Culture is a Person.</p></div>
<div class="strategy-box" style="left:385px;background:var(--red)"><h4><span></span>Heart Emotions</h4><p>80% of the decisions we make are motivated by our emotions, so when it comes to culture, emotional intelligence.</p></div>
<div class="strategy-box" style="left:611px;background:var(--purple)"><h4><span></span>Soul Intuition</h4><p>If Culture is a person, then our culture must have soul. We like to think of it as intuition. That invisible yet tangible piece.</p></div>
<div class="strategy-box" style="left:835px;background:var(--gold)"><h4><span></span>Strength Energy</h4><p>As humans, we each have an inner strength enabling us to accomplish our dreams and goals. Companies also have a version.</p></div>

<!-- footer -->
<footer class="site-footer" role="img" aria-label="Dim photo of people working at a table in a modern office, dark overlay"></footer>
<h2 class="sec-head center footer-head" style="top:3252px"><span class="sq" style="background:#fff"></span>Connect Us</h2>

<div class="field" style="left:161px;top:3362px;width:187px">Name:<i></i></div>
<div class="field" style="left:360px;top:3362px;width:187px">Email:<i></i></div>
<div class="field" style="left:161px;top:3411px;width:187px">Phone:<i></i></div>
<div class="field" style="left:360px;top:3411px;width:187px">Subject:<i></i></div>
<div class="field" style="left:161px;top:3460px;width:386px;height:70px">Message:<i style="align-self:center"></i></div>
<a class="btn btn-submit">SUBMIT</a>

<div class="social"><span></span><span></span><span></span><span></span><span></span></div>
<nav class="footer-nav"><span>Events</span><span>|</span><span>Expand</span><span>|</span><span>X</span><span>|</span><span>About</span><span>|</span><span>Connect</span></nav>
<div class="footer-contact" style="left:645px"><b><svg width="12" height="12" viewBox="0 0 24 24"><path d="M6.6 10.8a15 15 0 006.6 6.6l2.2-2.2a1 1 0 011-.25 11.4 11.4 0 003.6.57 1 1 0 011 1V20a1 1 0 01-1 1A17 17 0 013 4a1 1 0 011-1h3.5a1 1 0 011 1c0 1.250.2 2.45.57 3.6a1 1 0 01-.25 1z" fill="#fff"/></svg></b>+1-555-010-7890</div>
<div class="footer-contact" style="left:828px"><b><svg width="13" height="10" viewBox="0 0 13 10"><rect x="0.75" y="0.75" width="11.5" height="8.5" fill="none" stroke="#fff" stroke-width="1.3"/><path d="M1 1l5.5 4.5L12 1" fill="none" stroke="#fff" stroke-width="1.3"/></svg></b>connect@brevlon.example</div>
<div class="footer-rule"></div>
<p class="copyright">©2019 <em>BREVLON</em>. All Right Reserved. | Terms &amp; Conditions</p>

</body>
</html>
```